Brell Stone Company Business Cards

Front and Back Business Card - logo and text setup - cool design. I need workable photoshop or illustrator files so I can setup each employee card with design that is created
Updates

Hi everyone, thank you for the great entries. Please no more white and blue cards - there are so many already - black and silver only now please. thanks!

Target Market(s)

Construction Industry - Facility Managers

Industry/Entity Type

Construction

Contact Information for Business Card

I really like contemporary simplistic looks - clean neat....not opposed to seeing some black backrounds

Requirements
Must have
• Logo/website address with design on front only - www.brellstone-example.com (logo attached)
• Back:
• Name/Title/Company Address/Phone/email address
Nice to have
• Cool design
Should not have
• Nothing gimmicky like Fire or Water - since we are a Fire Protection company - it has all been done

```html
<!DOCTYPE html>
<html lang="en">
<head>
<meta charset="utf-8">
<title>Brell Stone Company Business Cards</title>
<link href="https://fonts.googleapis.com/css2?family=Lato:wght@400;700;900&display=swap" rel="stylesheet">
<style>
  :root {
    --backdrop: #3b3b3b;
    --card-dark: #2b2b2c;
    --card-dark-glow: #6a6a6b;
    --silver-light: #e4e5e7;
    --silver-mid: #c9cbce;
    --ink-light: #f2f2f2;
    --charcoal: #1f1f21;
    --silver-accent: #7c7f84;
    --grey-text: #4a4b4e;
    --rule: #7a7a7d;
  }
  * { margin: 0; padding: 0; box-sizing: border-box; }
  html, body {
    width: 1200px; height: 829px; overflow: hidden;
    background: var(--backdrop);
    font-family: "Lato", sans-serif;
  }
  .card {
    position: absolute;
    top: 282px;
    width: 485px;
    height: 278px;
    box-shadow: 0 4px 14px rgba(0,0,0,0.45);
  }
  .card--front {
    left: 82px;
    background: radial-gradient(ellipse 55% 75% at 50% 55%, var(--card-dark-glow) 0%, #454546 45%, var(--card-dark) 100%);
  }
  .card--back {
    left: 628px;
    background: linear-gradient(135deg, var(--silver-light) 0%, #f0f1f2 45%, var(--silver-mid) 100%);
  }
  .wordmark {
    position: absolute;
    left: 0; right: 0;
    text-align: center;
    font-weight: 900;
    letter-spacing: -0.5px;
    line-height: 1;
  }
  .card--front .wordmark {
    top: 108px;
    font-size: 50px;
    color: var(--ink-light);
  }
  .card--back .wordmark {
    top: 48px;
    font-size: 40px;
    color: var(--charcoal);
  }
  .web-line {
    position: absolute;
    left: 107px; right: 107px;
    top: 230px;
    display: flex;
    align-items: center;
    gap: 8px;
    color: var(--ink-light);
    font-size: 11.5px;
    letter-spacing: 1px;
  }
  .web-line::before, .web-line::after {
    content: ""; flex: 1; height: 1px; background: var(--ink-light); opacity: 0.85;
  }
  .web-line strong { font-weight: 700; }
  .person {
    position: absolute;
    right: 271px;
    top: 186px;
    text-align: right;
  }
  .person__name { font-size: 17px; font-weight: 700; color: var(--charcoal); line-height: 1.15; }
  .person__name .surname { color: var(--silver-accent); }
  .person__title { font-size: 13px; color: var(--grey-text); }
  .divider {
    position: absolute;
    left: 240px; top: 168px;
    width: 1px; height: 72px;
    background: var(--rule);
  }
  .contact {
    position: absolute;
    left: 268px; top: 165px;
    font-size: 13px;
    color: var(--grey-text);
    line-height: 16.5px;
  }
  .contact__address { margin-bottom: 7px; }
  .contact__row { display: flex; align-items: center; gap: 5px; }
  .contact__row svg { width: 10px; height: 10px; flex: none; }
</style>
</head>
<body>
  <section class="card card--front" aria-label="Card front">
    <div class="wordmark">Brell Stone</div>
    <div class="web-line"><span>www.<strong>brellstone-example</strong>.com</span></div>
  </section>

  <section class="card card--back" aria-label="Card back">
    <div class="wordmark">Brell Stone</div>
    <div class="person">
      <div class="person__name">Daniel <span class="surname">Harper</span></div>
      <div class="person__title">Managing Director</div>
    </div>
    <div class="divider"></div>
    <div class="contact">
      <div class="contact__address">Co. Street, Suite, Building<br>City/State, Zip Code</div>
      <div class="contact__row">
        <svg viewBox="0 0 10 10" aria-hidden="true"><path d="M2 1 L3.6 1 L4.2 3 L3.2 3.8 Q4.2 5.8 6.2 6.8 L7 5.8 L9 6.4 L9 8 Q8.4 9 7 9 Q1 8 1 2.4 Q1 1 2 1 Z" fill="var(--charcoal)"/></svg>
        <span>300.555.0199</span>
      </div>
      <div class="contact__row">
        <svg viewBox="0 0 10 10" aria-hidden="true"><rect x="0.8" y="2" width="8.4" height="6" fill="none" stroke="var(--charcoal)" stroke-width="1"/><path d="M0.8 2 L5 5.4 L9.2 2" fill="none" stroke="var(--charcoal)" stroke-width="1"/></svg>
        <span>info@brellstone-example.com</span>
      </div>
    </div>
  </section>
</body>
</html>
```